Luxury travel agency needs a website design

We are a travel agency specializing in booking luxury vacations. We specialize in Hawaii, Europe and Caribbean, but will do all vacations. I want a very classy website design which would attract luxury clients. The company name is "Harbors and Hammocks Travel Agency". Would love the web design to go with the color scheme of the logo. Hex codes included in files. Logo is attached. Would also love more Grey in the website. I want it very elegant

Coding

Coded - Design and coding required

Font styles to use
Sans Serif
Decorative

Requirements
Must have
• - Consultation Tab or a page where the client can fill out a short form about what vacation that they would want to book. I want this info to be sent to me in order for me to contact them.
- Somewhere with my contact info "email: marla@harborsandhammockstravel.example and phone number"
- Social media links
- About section "Marla Dunbevy - Agency Owner (picture provided)
Marla has been traveling full time for the passed two years and has been very passionate about travel from a young age. Marla is dedicated to working closely with clients to book their dream vacation.
Marla's specializations include honeymoons and anniversaries focusing on travel in Europe, Hawaii and all inclusive resorts in the Caribbean.

```html
<!DOCTYPE html>
<html lang="en">
<head>
<meta charset="utf-8">
<title>Harbors and Hammocks Travel Agency – Schedule a Consult</title>
<link href="https://fonts.googleapis.com/css2?family=Montserrat:wght@400;500;600;700&family=Patrick+Hand+SC&display=swap" rel="stylesheet">
<style>
:root{
  --orange:#f28a4b;
  --ink:#1c1c1c;
  --grey:#6d6d6d;
  --grey-line:#4a4a4a;
  --grey-text:#d8d8d8;
  --white:#ffffff;
}
*{margin:0;padding:0;box-sizing:border-box}
html,body{width:741px;height:1200px;overflow:hidden;background:var(--white)}
body{position:relative;font-family:"Montserrat",Arial,sans-serif;color:var(--ink)}
.page{position:relative;width:741px;height:1200px;overflow:hidden}

/* top bar */
.topbar{position:absolute;top:0;left:0;width:100%;height:20px;background:rgba(20,20,30,.55);z-index:5;
  display:flex;align-items:center;justify-content:space-between;padding:0 110px;font-size:7px;color:var(--white)}
.topbar .contact-item{display:flex;align-items:center;gap:5px}
.topbar .dot{width:8px;height:8px;border-radius:50%;background:var(--orange);display:inline-block}
.topbar .right{display:flex;align-items:center;gap:10px}
.socials{display:flex;gap:4px}
.socials span{width:9px;height:9px;border-radius:50%;background:var(--orange)}

/* hero */
.hero{position:absolute;top:0;left:0;width:741px;height:340px}
.hero-photo{position:absolute;inset:0;background:linear-gradient(180deg,#5b5a86 0%,#a87796 28%,#f2a98b 48%,#f6c892 56%,#6f8fa8 62%,#2f4d66 80%,#1f3446 100%)}
.hero-wave{position:absolute;left:0;bottom:0;width:741px;height:90px}
.nav{position:absolute;top:28px;left:100px;right:100px;display:flex;align-items:center;justify-content:space-between;z-index:4}
.brand{display:flex;align-items:center;gap:7px;font-weight:700;font-size:11px;color:var(--ink);line-height:1.15;width:150px}
.brand .mark{width:14px;height:14px;border-radius:50%;background:var(--orange);flex:none}
.nav-links{display:flex;align-items:center;gap:22px;font-size:8px;font-weight:600;color:var(--white);letter-spacing:.5px}
.nav-cta{background:var(--ink);color:var(--white);padding:7px 12px;border-radius:14px;font-size:7.5px;font-weight:600}
.hero-title{position:absolute;right:110px;top:138px;width:200px;text-align:center;font-family:"Patrick Hand SC",cursive;font-weight:400;font-size:40px;line-height:1;color:var(--white);letter-spacing:1px}

/* consult section */
.consult{position:absolute;top:340px;left:0;width:741px;height:300px;text-align:center}
.consult h2{position:absolute;top:68px;left:0;width:100%;font-family:"Patrick Hand SC",cursive;font-weight:400;font-size:30px;color:var(--ink);letter-spacing:1px}
.accent{color:var(--orange)}
.consult p{position:absolute;top:118px;left:110px;width:521px;font-size:6.8px;line-height:1.75;color:var(--grey)}
.consult .btn{position:absolute;top:172px;left:283px;width:175px;height:30px;line-height:30px;border-radius:15px;background:var(--orange);color:var(--white);font-size:7px;font-weight:600;letter-spacing:.4px}

/* scenic band */
.scenic{position:absolute;top:640px;left:0;width:741px;height:310px}
.scenic-photo{position:absolute;inset:0;background:linear-gradient(180deg,#3e6f96 0%,#7fa7c4 30%,#c7b79a 48%,#2f6c5a 58%,#2b7c8c 72%,#1d5d78 100%)}
.scenic-edges{position:absolute;inset:0;width:741px;height:310px}
.scenic-name{position:absolute;top:92px;left:0;width:100%;text-align:center;font-weight:700;font-size:30px;color:var(--white);letter-spacing:.5px;line-height:1.2}
.scenic-name .sub{display:block;margin-top:6px;font-size:13px;letter-spacing:3px}

/* footer */
.footer{position:absolute;top:940px;left:0;width:741px;height:260px;background:var(--ink);color:var(--white)}
.footer-brand{position:absolute;top:70px;left:132px;display:flex;align-items:center;gap:8px;font-weight:700;font-size:14px;line-height:1.2;width:190px}
.footer-brand .mark{width:16px;height:16px;border-radius:50%;background:var(--orange);flex:none}
.col-title{font-size:9px;font-weight:600;letter-spacing:.6px;margin-bottom:10px}
.quick-links{position:absolute;top:34px;left:352px}
.quick-links li{list-style:none;font-size:7.5px;line-height:17px;color:var(--grey-text)}
.newsletter{position:absolute;top:34px;left:482px;width:150px}
.newsletter .field{margin-top:6px;width:150px;height:30px;border-radius:15px;background:var(--white);color:var(--ink);font-size:7.5px;line-height:30px;padding-left:14px}
.newsletter .subscribe{margin-top:10px;width:78px;height:26px;border-radius:13px;background:var(--orange);font-size:7px;font-weight:600;line-height:26px;text-align:center}
.footer hr{position:absolute;top:190px;left:112px;width:517px;border:none;border-top:1px solid var(--grey-line)}
.copyright{position:absolute;top:222px;left:0;width:100%;text-align:center;font-size:7px;color:var(--grey-text)}
</style>
</head>
<body>
<div class="page">

  <div class="topbar">
    <div class="contact-item"><span class="dot"></span>marla@harborsandhammockstravel.example</div>
    <div class="right">
      <div class="contact-item"><span class="dot"></span>(808) 555-0142</div>
      <div class="socials"><span></span><span></span><span></span></div>
    </div>
  </div>

  <header class="hero">
    <div class="hero-photo" role="img" aria-label="Sunset over a tropical beach with rocks and palm leaves"></div>
    <svg class="hero-wave" viewBox="0 0 741 90" preserveAspectRatio="none" aria-hidden="true">
      <path d="M0 60 C150 20 300 10 420 40 C560 75 660 40 741 20 L741 90 L0 90 Z" fill="#ffffff"/>
    </svg>
    <nav class="nav">
      <div class="brand"><span class="mark"></span>Harbors &amp; Hammocks Travel Agency</div>
      <div class="nav-links">
        <span>HOME</span><span>ABOUT</span><span>CONTACT</span>
        <span class="nav-cta">SCHEDULE A CONSULT</span>
      </div>
    </nav>
    <h1 class="hero-title">Schedule A Consult</h1>
  </header>

  <section class="consult">
    <h2>Schedule <span class="accent">A</span> Consult</h2>
    <p>Tell us where you dream of going, when you hope to travel and who is coming along. Marla will review your wishes and reach out personally to plan every detail of your luxury escape, from flights and villas to private tours and dinners.</p>
    <div class="btn">CLICK HERE TO SCHEDULE A CONSULT</div>
  </section>

  <section class="scenic">
    <div class="scenic-photo" role="img" aria-label="Aerial view of a tropical island at sunset"></div>
    <svg class="scenic-edges" viewBox="0 0 741 310" preserveAspectRatio="none" aria-hidden="true">
      <path d="M0 0 L741 0 L741 8 C560 0 420 30 300 20 C180 10 80 0 0 14 Z" fill="#ffffff"/>
      <path d="M0 300 C150 270 320 240 460 250 C600 260 690 280 741 290 L741 310 L0 310 Z" fill="#f28a4b"/>
      <path d="M0 306 C150 278 320 250 460 258 C600 266 690 286 741 296 L741 310 L0 310 Z" fill="#1c1c1c"/>
    </svg>
    <div class="scenic-name">Harbors &amp; Hammocks<span class="sub">TRAVEL AGENCY</span></div>
  </section>

  <footer class="footer">
    <div class="footer-brand"><span class="mark"></span>Harbors &amp; Hammocks Travel Agency</div>
    <div class="quick-links">
      <div class="col-title">QUICK LINKS</div>
      <ul><li>Home</li><li>About Us</li><li>Contact Us</li><li>Schedule a Consult</li></ul>
    </div>
    <div class="newsletter">
      <div class="col-title">SUBSCRIBE TO OUR NEWSLETTER</div>
      <div class="field">Email</div>
      <div class="subscribe">SUBSCRIBE</div>
    </div>
    <hr>
    <div class="copyright">Copyrights @ 2021 Harbors and Hammocks. All Rights Reserved.</div>
  </footer>

</div>
</body>
</html>
```